Business Cards and Stationary for a new consulting, recruiting and outsourcing company in Germany
WENDRACH Consulting
Business Cards and Stationary for a new consulting, recruiting and outsourcing company in Germany  - Consulting
Creative Brief
Professional
WENDRACH Consulting (Company Name) Rasa Wendrach (First name, last name)
Inhaberin ("Owner" for english version)
Im Birkenfeld 5 72614 Lautenbach Deutschland ("Germany" for english version)
rasa.wendrach@wendrach-beispiel.com
htttps://www.wendrach-beispiel.com
The round logo version with black background size around 75% of the card.

```html
<!DOCTYPE html>
<html lang="de">
<head>
<meta charset="utf-8">
<title>WENDRACH Consulting – Geschäftsausstattung</title>
<link href="https://fonts.googleapis.com/css2?family=Open+Sans:wght@400;600&display=swap" rel="stylesheet">
<style>
:root{
  --bg:#e9ebee;
  --paper:#ffffff;
  --blue:#29abe2;
  --green:#8cc63f;
  --ink:#4a4a4a;
  --ink-light:#8a8a8a;
  --black:#111111;
  --font:"Open Sans",Arial,sans-serif;
}
*{margin:0;padding:0;box-sizing:border-box}
html,body{width:1200px;height:936px;overflow:hidden}
body{background:var(--bg);font-family:var(--font);color:var(--ink);position:relative}
.sheet{position:absolute;background:var(--paper);overflow:hidden}
.footer-band{position:absolute;left:0;bottom:0;width:100%;background:var(--blue)}
.footer-rule{position:absolute;left:0;width:100%;background:var(--green)}
.brand{display:flex;align-items:center;gap:8px;white-space:nowrap}
.brand-dot{border-radius:50%;background:var(--blue);flex:none}
.brand-name{color:var(--ink);font-weight:600;line-height:1}
.web{position:absolute;color:#fff;font-size:11px;letter-spacing:.12em;white-space:nowrap}

/* letterhead */
.letterhead{left:183px;top:56px;width:391px;height:559px}
.letterhead .brand{position:absolute;left:42px;top:36px}
.letterhead .brand-dot{width:24px;height:24px}
.letterhead .brand-name{font-size:14px}
.letter-contact{position:absolute;right:30px;top:30px;text-align:right;font-size:5.5px;line-height:1.6;color:var(--ink-light);font-style:normal}
.letter-body{position:absolute;left:40px;top:112px;width:300px;font-size:5.5px;line-height:1.65;color:var(--ink-light)}
.letter-body p{margin-bottom:9px}
.letter-body .sig{font-size:14px;color:var(--ink);margin:4px 0 2px;font-style:italic}
.letterhead .footer-band{height:54px}
.letterhead .footer-rule{bottom:62px;height:4px}

/* folder */
.folder{left:630px;top:46px;width:467px;height:619px}
.folder .brand{position:absolute;left:60px;top:264px;gap:12px}
.folder .brand-dot{width:42px;height:42px}
.folder .brand-name{font-size:27px}
.folder .footer-band{height:74px}
.folder .footer-rule{bottom:84px;height:5px}
.folder .web{left:26px;bottom:27px}

/* business cards */
.card-front{left:46px;top:673px;width:178px;height:94px}
.card-front .brand{position:absolute;left:8px;top:18px;gap:5px}
.card-front .brand-dot{width:14px;height:14px}
.card-front .brand-name{font-size:8.5px}
.card-front .footer-band{height:20px}
.card-front .footer-rule{bottom:24px;height:3px}
.card-back{left:46px;top:780px;width:178px;height:96px;background:var(--black);display:flex;flex-direction:column;align-items:center;justify-content:center;gap:6px}
.card-back .brand-dot{width:40px;height:40px}
.card-back .brand-name{color:#fff;font-size:10px}

/* envelope */
.envelope{left:264px;top:673px;width:442px;height:203px}
.envelope .brand{position:absolute;left:38px;top:40px}
.envelope .brand-dot{width:24px;height:24px}
.envelope .brand-name{font-size:15px}
.envelope .footer-band{height:40px}
.envelope .footer-rule{bottom:46px;height:4px}
.envelope .web{left:22px;bottom:14px;font-size:9px}

/* envelope back */
.envelope-back{left:739px;top:673px;width:412px;height:203px}
.flap{position:absolute;left:0;top:0;width:100%;height:46px;background:var(--blue)}
.envelope-back .web{left:150px;top:17px;font-size:11px}
</style>
</head>
<body>

<section class="sheet letterhead">
  <div class="brand"><span class="brand-dot"></span><span class="brand-name">WENDRACH Consulting</span></div>
  <address class="letter-contact">
    Rasa Wendrach<br>Im Birkenfeld 5<br>72614 Lautenbach<br>rasa.wendrach@wendrach-beispiel.com<br>www.wendrach-beispiel.com
  </address>
  <div class="letter-body">
    <p>July 1, 2024</p>
    <p>Dear Client<br>123 Sample Street, Town</p>
    <p>Thank you for your interest in our consulting services. We support growing companies with recruiting, outsourcing and strategic advice, and we would be glad to discuss how our team can help you reach your goals with clarity and care.</p>
    <p>Our approach is practical and personal. We listen first, then build a plan that fits your structure, your people and your budget.</p>
    <p>Please contact us at any time to arrange a first meeting. We look forward to working together with you.</p>
    <p>Kind regards</p>
    <div class="sig">Rasa</div>
    <p>Rasa Wendrach<br>Inhaberin</p>
  </div>
  <div class="footer-rule"></div>
  <div class="footer-band"></div>
</section>

<section class="sheet folder">
  <div class="brand"><span class="brand-dot"></span><span class="brand-name">WENDRACH Consulting</span></div>
  <div class="footer-rule"></div>
  <div class="footer-band"></div>
  <div class="web">www.wendrach-beispiel.com</div>
</section>

<section class="sheet card-front">
  <div class="brand"><span class="brand-dot"></span><span class="brand-name">WENDRACH Consulting</span></div>
  <div class="footer-rule"></div>
  <div class="footer-band"></div>
</section>

<section class="sheet card-back">
  <span class="brand-dot"></span>
  <span class="brand-name">WENDRACH Consulting</span>
</section>

<section class="sheet envelope">
  <div class="brand"><span class="brand-dot"></span><span class="brand-name">WENDRACH Consulting</span></div>
  <div class="footer-rule"></div>
  <div class="footer-band"></div>
  <div class="web">www.wendrach-beispiel.com</div>
</section>

<section class="sheet envelope-back">
  <div class="flap"></div>
  <div class="web">www.wendrach-beispiel.com</div>
</section>

</body>
</html>
```